Upmarket Dessert Lounge needs a Business Card Design

We are an upmarket dessert lounge needing a business card to match our image.

We want something that is simple yet beautiful, feminine, classy, sophisticated and elegant. We want it to stand out and don't mind if it is bold.

The design should include our logo and colours of red or maroon with gold highlights. We don't mind if black is used.

Marlow & Quince

Target Market(s)

For those who like to indulge or treat themselves and give in to their temptations on good quality desserts.

Industry/Entity Type

Business

Requirements
Must have
• Must include our logo and our name

Marlow & Quince

M & Q

```html
<!DOCTYPE html>
<html lang="en">
<head>
<meta charset="utf-8">
<title>Marlow &amp; Quince — Business Card</title>
<link rel="stylesheet" href="https://fonts.googleapis.com/css2?family=Source+Sans+3:wght@400;600;700&display=swap">
<style>
  :root {
    --page-bg: #e4e4e4;
    --card-black: #000000;
    --maroon: #7a1416;
    --gold: #f7cd92;
    --white: #ffffff;
  }
  * { margin: 0; padding: 0; box-sizing: border-box; }
  html, body {
    width: 956px;
    height: 1200px;
    overflow: hidden;
    background: var(--page-bg);
    font-family: "Source Sans 3", sans-serif;
  }
  .canvas { position: relative; width: 956px; height: 1200px; }
  .card {
    position: absolute;
    width: 797px;
    height: 456px;
    background: var(--card-black);
    border-radius: 30px;
    overflow: hidden;
  }
  .card--front { left: 83px; top: 93px; }
  .card--back { left: 75px; top: 633px; }

  .brand-name {
    position: absolute;
    color: var(--gold);
    font-weight: 600;
    white-space: nowrap;
    transform: translate(-50%, -50%);
    line-height: 1;
  }
  .brand-name--front { left: 235px; top: 182px; font-size: 42px; letter-spacing: 1px; }
  .brand-name--back { left: 395px; top: 232px; font-size: 110px; letter-spacing: 2px; }

  .person { position: absolute; left: 471px; top: 82px; color: var(--gold); line-height: 1.2; }
  .person__name { font-size: 21px; font-weight: 700; }
  .person__role { font-size: 22px; font-weight: 400; }

  .contact { position: absolute; left: 471px; top: 152px; color: var(--white); font-size: 19px; list-style: none; }
  .contact li { height: 30px; line-height: 30px; }
  .contact li.contact__gap { margin-top: 2px; }
  .contact b { font-weight: 700; }

  .wave { position: absolute; left: 0; top: 0; }

  .address {
    position: absolute;
    left: 574px; top: 389px;
    transform: translateX(-50%);
    color: var(--white);
    font-size: 18px;
    line-height: 27px;
    text-align: center;
    white-space: nowrap;
  }
</style>
</head>
<body>
<main class="canvas">
  <section class="card card--front">
    <svg class="wave" width="797" height="456" viewBox="0 0 797 456" aria-hidden="true">
      <path fill="var(--gold)" d="M0,400 C150,428 300,392 420,345 C560,298 700,318 797,352 L797,372 C700,342 560,328 420,372 C300,414 150,442 0,422 Z"/>
      <path fill="var(--maroon)" d="M0,422 C150,442 300,414 420,372 C560,328 700,342 797,372 L797,456 L0,456 Z"/>
      <path fill="var(--gold)" d="M410,402 C560,338 700,348 797,384 L797,396 C700,364 560,358 410,402 Z"/>
    </svg>

    <div class="brand-name brand-name--front">MARLOW &amp; QUINCE</div>

    <div class="person">
      <div class="person__name">Your Name</div>
      <div class="person__role">Designation</div>
    </div>

    <ul class="contact">
      <li><b>p</b> : 123-456-7890</li>
      <li><b>c</b> : 123-456-7890</li>
      <li><b>f</b> : 123-456-7890</li>
      <li class="contact__gap"><b>e</b> : name@yourwebsite.com</li>
      <li><b>w</b> : www.marlowquince.com</li>
    </ul>

    <address class="address" style="font-style: normal;">
      0000, Street Name<br>City Name, Country Code.
    </address>
  </section>

  <section class="card card--back">
    <div class="brand-name brand-name--back">M&amp;Q</div>
  </section>
</main>
</body>
</html>
```